Heron Loan Partners Business Card

We need a business card design for our mortgage servicing company. In addition to servicing the loans of homeowners, we help homeowners with purchasing their homes and any mortgage refinancing. We would like to see designs that use the colors in the logo attached below (gold-ish yellow and navy blue), and any other design you deem fit! The design should communicate a simpler life with smart mortgages provided by Heron.

```html
<!DOCTYPE html>
<html lang="en">
<head>
<meta charset="utf-8">
<title>Heron Loan Partners – Business Card</title>
<link href="https://fonts.googleapis.com/css2?family=Open+Sans:wght@400;600;700;800&display=swap" rel="stylesheet">
<style>
  :root {
    --stage: #242424;
    --card: #1f1f23;
    --gold: #e0af3a;
    --white: #ffffff;
    --emboss: #2a2a2f;
    --emboss-edge: #34343a;
  }
  * { box-sizing: border-box; margin: 0; padding: 0; }
  html, body { width: 1200px; height: 780px; overflow: hidden; }
  body {
    background: var(--stage);
    font-family: "Open Sans", Arial, sans-serif;
    position: relative;
  }
  .card {
    position: absolute;
    width: 540px;
    height: 310px;
    background: var(--card);
    border-left: 4px solid var(--gold);
    border-bottom: 4px solid var(--gold);
    box-shadow: 0 18px 40px rgba(0,0,0,.55);
    overflow: hidden;
  }
  .card--front { left: 45px; top: 235px; }
  .card--back { left: 615px; top: 235px; }

  .wordmark {
    position: absolute;
    font-weight: 800;
    color: var(--gold);
    letter-spacing: .5px;
    white-space: nowrap;
  }
  .card--front .wordmark {
    left: 0; right: 0; top: 118px;
    text-align: center;
    font-size: 52px;
  }
  .card--back .wordmark { left: 34px; top: 34px; font-size: 28px; }
  .wordmark-faint {
    position: absolute;
    right: 26px; bottom: 30px;
    font-size: 58px;
    font-weight: 800;
    color: var(--emboss);
    text-shadow: 1px 1px 0 var(--emboss-edge), -1px -1px 0 #18181b;
    white-space: nowrap;
  }

  .holder {
    position: absolute;
    right: 34px; top: 30px;
    text-align: right;
  }
  .holder-name { font-size: 24px; font-weight: 700; line-height: 1.1; }
  .holder-name .first { color: var(--gold); }
  .holder-name .last { color: var(--white); }
  .holder-title { color: var(--white); font-size: 13px; margin-top: 3px; }
  .accent-bar {
    position: absolute;
    right: 0; top: 24px;
    width: 20px; height: 52px;
    background: var(--gold);
  }

  .contact {
    position: absolute;
    left: 34px; bottom: 30px;
    color: var(--white);
    font-size: 13.5px;
    line-height: 1.45;
  }
  .contact-address { margin-bottom: 10px; }
  .contact-list { list-style: none; }
  .contact-list li { display: flex; align-items: center; gap: 8px; }
  .contact-list svg { width: 13px; height: 13px; fill: var(--gold); flex: none; }
</style>
</head>
<body>
  <section class="card card--front" aria-label="Card front">
    <div class="wordmark">Heron Mortgage</div>
  </section>

  <section class="card card--back" aria-label="Card back">
    <div class="wordmark">Heron Mortgage</div>

    <div class="holder">
      <p class="holder-name"><span class="first">Lena</span> <span class="last">Marovic</span></p>
      <p class="holder-title">Managing Director</p>
    </div>
    <div class="accent-bar"></div>

    <div class="wordmark-faint" aria-hidden="true">Heron</div>

    <div class="contact">
      <p class="contact-address">1840 Willow Bend Rd. Suite 300<br>Dallas, TX 75201</p>
      <ul class="contact-list">
        <li>
          <svg viewBox="0 0 24 24" aria-hidden="true"><path d="M6.6 10.8a15.1 15.1 0 0 0 6.6 6.6l2.2-2.2a1 1 0 0 1 1-.25 11.4 11.4 0 0 0 3.6.57 1 1 0 0 1 1 1V20a1 1 0 0 1-1 1A17 17 0 0 1 3 4a1 1 0 0 1 1-1h3.5a1 1 0 0 1 1 1c0 1.25.2 2.45.57 3.57a1 1 0 0 1-.25 1z"/></svg>
          (555) 214-3690
        </li>
        <li>
          <svg viewBox="0 0 24 24" aria-hidden="true"><path d="M2 5h20v14H2zm2 2v.5l8 5 8-5V7zm0 2.9V17h16V9.9l-8 5z"/></svg>
          info@heronloan.com
        </li>
        <li>
          <svg viewBox="0 0 24 24" aria-hidden="true"><path d="M12 2a10 10 0 1 0 0 20 10 10 0 0 0 0-20zm6.9 6h-3a15.6 15.6 0 0 0-1.4-3.6A8 8 0 0 1 18.9 8zM12 4c.8 1.2 1.5 2.5 1.9 4h-3.8c.4-1.5 1.1-2.8 1.9-4zM4.3 14a8 8 0 0 1 0-4h3.4a16 16 0 0 0 0 4zm.8 2h3a15.6 15.6 0 0 0 1.4 3.6A8 8 0 0 1 5.1 16zm3-8h-3a8 8 0 0 1 4.4-3.6A15.6 15.6 0 0 0 8.1 8zM12 20c-.8-1.2-1.5-2.5-1.9-4h3.8c-.4 1.5-1.1 2.8-1.9 4zm2.3-6H9.7a14.7 14.7 0 0 1 0-4h4.6a14.7 14.7 0 0 1 0 4zm.2 5.6a15.6 15.6 0 0 0 1.4-3.6h3a8 8 0 0 1-4.4 3.6zm1.8-5.6a16 16 0 0 0 0-4h3.4a8 8 0 0 1 0 4z"/></svg>
          www.heronloan.com
        </li>
      </ul>
    </div>
  </section>
</body>
</html>
```